SaaS Early tech startup business card design

Unique design for experience ecommerce platform company. the business cards will be used by executive members. conformance with color code is required.

```html
<!DOCTYPE html>
<html lang="en">
<head>
<meta charset="utf-8">
<title>Novik Business Card</title>
<link href="https://fonts.googleapis.com/css2?family=Lato:wght@400;700;900&family=Arimo:wght@400&display=swap" rel="stylesheet">
<style>
  :root {
    --stage-bg: #000000;
    --card-bg: #2f3033;
    --card-stripe: rgba(255, 255, 255, 0.018);
    --teal: #17a3a6;
    --teal-name: #1aa2a8;
    --text-light: #f2f2f2;
    --divider: #45474b;
  }
  * { margin: 0; padding: 0; box-sizing: border-box; }
  html, body {
    width: 1200px;
    height: 900px;
    overflow: hidden;
    background: var(--stage-bg);
  }
  .stage {
    position: relative;
    width: 1200px;
    height: 900px;
  }
  .card {
    position: absolute;
    width: 458px;
    height: 282px;
    border-radius: 15px;
    background-color: var(--card-bg);
    background-image: repeating-linear-gradient(90deg, var(--card-stripe) 0 1px, transparent 1px 3px);
  }
  .card--front { left: 138px; top: 265px; }
  .card--back { left: 625px; top: 268px; }

  .brand {
    position: absolute;
    font-family: "Lato", sans-serif;
    font-weight: 900;
    color: var(--teal);
    letter-spacing: 1px;
    line-height: 1;
  }
  .card--front .brand {
    left: 30px;
    top: 104px;
    font-size: 66px;
  }
  .card--back .brand {
    left: 0;
    right: 0;
    top: 94px;
    text-align: center;
    font-size: 80px;
  }

  .divider {
    position: absolute;
    left: 232px;
    top: 56px;
    width: 1px;
    height: 160px;
    background: var(--divider);
  }

  .details {
    position: absolute;
    left: 253px;
    top: 70px;
    font-family: "Arimo", sans-serif;
    color: var(--text-light);
  }
  .person-name {
    font-family: "Lato", sans-serif;
    font-weight: 700;
    font-size: 19px;
    color: var(--teal-name);
    letter-spacing: -0.3px;
    line-height: 22px;
  }
  .person-role {
    font-size: 13.5px;
    line-height: 17px;
    margin-top: -1px;
  }
  .contact-list {
    list-style: none;
    margin-top: 9px;
  }
  .contact-item {
    display: flex;
    align-items: center;
    gap: 4px;
    font-size: 13.5px;
    line-height: 17px;
  }
  .contact-icon {
    width: 12px;
    height: 12px;
    flex: none;
  }
  .address {
    font-size: 13.5px;
    line-height: 16.5px;
    margin-top: 9px;
    font-style: normal;
  }
</style>
</head>
<body>
<main class="stage">
  <section class="card card--front">
    <div class="brand">novik</div>
    <div class="divider"></div>
    <div class="details">
      <h1 class="person-name">DANIEL REYES</h1>
      <p class="person-role">Managing Director</p>
      <ul class="contact-list">
        <li class="contact-item">
          <svg class="contact-icon" viewBox="0 0 12 12" aria-hidden="true">
            <path d="M2.5 1 L4.5 3.2 L3.6 4.6 C4.2 6 5.8 7.6 7.4 8.4 L8.8 7.5 L11 9.5 L9.8 11 C5.5 10.6 1.4 6.5 1 2.2 Z" fill="none" stroke="var(--teal)" stroke-width="1.1" stroke-linejoin="round"/>
            <path d="M7 2.2 A3 3 0 0 1 9.8 5 M7 0.6 A4.5 4.5 0 0 1 11.4 5" fill="none" stroke="var(--teal)" stroke-width="0.9"/>
          </svg>
          044-987 654 321
        </li>
        <li class="contact-item">
          <svg class="contact-icon" viewBox="0 0 12 12" aria-hidden="true">
            <rect x="0.5" y="2.5" width="11" height="7.5" fill="var(--teal)"/>
            <path d="M0.5 2.5 L6 7 L11.5 2.5 M0.5 10 L4.5 6 M11.5 10 L7.5 6" fill="none" stroke="var(--card-bg)" stroke-width="0.9"/>
          </svg>
          hello@novikapp.com
        </li>
        <li class="contact-item">
          <svg class="contact-icon" viewBox="0 0 12 12" aria-hidden="true">
            <circle cx="6" cy="6" r="5.2" fill="none" stroke="var(--teal)" stroke-width="1"/>
            <ellipse cx="6" cy="6" rx="2.2" ry="5.2" fill="none" stroke="var(--teal)" stroke-width="0.8"/>
            <path d="M0.8 6 H11.2 M1.8 3.4 H10.2 M1.8 8.6 H10.2" stroke="var(--teal)" stroke-width="0.8"/>
          </svg>
          www.novikapp.com
        </li>
      </ul>
      <address class="address">
        421, Address line goes here<br>
        45452,Country Name
      </address>
    </div>
  </section>

  <section class="card card--back">
    <div class="brand">novik</div>
  </section>
</main>
</body>
</html>
```